Hardcore nerd needs to stand out in a sea of dull Defence business cards

Wombarra Devices is a new Australian consulting engineering company that turns research and theory into practical systems. No evangelistic fluff, just mathematics and physics into electronic and optical circuits for consumer products, scientific research or Defence applications.

We already have a recognised logo (provided) which is often dark blue/black on a light background but we're open to other combinations. (Us engineers tend to have limited aesthetic imagination :)

Some of our recent products have included:
* Instrumentation for electrical testing,
* Radar jammers,
* GPS antenna design,
* Satellite tracking systems,
* High power lasers

We're open to both single and double-sided designs - happy to be convinced either way.

P.S. Another group is working on the web page, so - alas - our web site is currently of no use for images/ideas...

Target Market(s)

Engineering managers,
Scientists

Contact Information for Business Card

Dr Colin Harte
R&D Engineer

colin@wombarradevices.com.au
0427 563 710

PO Box XXX (to be confirmed)
Kelsby ACT 2917
Australia

Font styles to use
Serif
Sans Serif

Colors

Designer to choose colors to be used in the design.

Requirements
Must have
• My contact details!
• I've had many (great) "bold and plain" designs submitted already, so feel free to be artistically creative :)
• Happy to take advice re fonts/colours/printability etc.
Nice to have
• I'm not sure if "lists" are more at home on a CV than a business card, but representative services include:
• Applied electromagnetics
• RF and high speed electronics
• Signal and image processing
• Electro-optical and laser systems
• Concept-to-prototype design services
• If you're considering double sided cards, then often measuring/alignment grids/rulers feature on the back of similar cards.
• e.g. https://www.veltranoptics.example/newgrouppage9.cfm?objectgroup_id=4183
• https://www.veltranoptics.example/newgrouppage9.cfm?objectgroup_ID=4185
• ..or even a "Smith chart" (google will return lots)
• Generic images to represent a capability might work - googling images associated with keyword for each of these areas might help:
• - "passive radar", "phased array", "fdtd", "vircator"
• RF and high speed electronic design
• - "smith chart", "microstrip circuits", "dimensioned drawing", "electronic schematic"
• - "dft", "iir filter"
• - "optical cavity". "laser energy level diagram"
• Background/watermarked images outlines/wireframes/schematics would probably look OK.
Should not have
• If a list of projects/services is provided, it is important not to make the client feel that this is "all" the company can do. Engineering design is a creative discipline (like graphics :)
• Please, no stock "military" snaps like planes, missiles, etc!

```html
<!DOCTYPE html>
<html lang="en">
<head>
<meta charset="utf-8">
<title>Wombarra Devices – Business Card</title>
<link rel="stylesheet" href="https://fonts.googleapis.com/css2?family=Arimo:wght@700&family=Lato:wght@400;700&display=swap">
<style>
  :root {
    --navy: #03215f;
    --navy-light: #2a4a88;
    --white: #ffffff;
    --backdrop: #e9e6e2;
    --shadow: rgba(0, 0, 0, 0.35);
  }
  * { box-sizing: border-box; margin: 0; padding: 0; }
  html, body {
    width: 1200px;
    height: 900px;
    overflow: hidden;
    background: var(--backdrop);
  }
  .canvas {
    position: relative;
    width: 1200px;
    height: 900px;
    font-family: "Lato", sans-serif;
  }
  .card {
    position: absolute;
    box-shadow: 3px 4px 6px var(--shadow);
    overflow: hidden;
  }

  /* Front */
  .card-front {
    left: 330px;
    top: 90px;
    width: 555px;
    height: 343px;
    background: var(--navy);
    color: var(--white);
  }
  .brand-mark-area {
    position: absolute;
    left: 290px;
    top: 40px;
    width: 265px;
    height: 303px;
    border-top-left-radius: 150px;
    background: linear-gradient(160deg, var(--navy-light) 0%, #8fa2c6 55%, var(--white) 100%);
  }
  .person {
    position: absolute;
    left: 31px;
    top: 54px;
  }
  .person-name {
    font-family: "Arimo", sans-serif;
    font-weight: 700;
    font-size: 20px;
    letter-spacing: 0.2px;
    line-height: 22px;
  }
  .person-role {
    font-size: 15px;
    line-height: 18px;
  }
  .address {
    position: absolute;
    left: 31px;
    top: 190px;
    font-style: normal;
    font-size: 16px;
    line-height: 20px;
  }
  .contact-list {
    position: absolute;
    left: 31px;
    top: 250px;
    list-style: none;
    font-size: 16px;
    line-height: 20px;
  }
  .contact-list li {
    display: flex;
    align-items: center;
    gap: 6px;
  }
  .contact-icon {
    width: 12px;
    height: 12px;
    fill: var(--white);
    flex: none;
  }

  /* Back */
  .card-back {
    left: 330px;
    top: 469px;
    width: 559px;
    height: 344px;
    background: var(--white);
  }
  .brand {
    position: absolute;
    left: 0;
    right: 0;
    top: 100px;
    display: flex;
    justify-content: center;
    align-items: center;
    gap: 14px;
  }
  .brand-dot {
    width: 34px;
    height: 34px;
    border-radius: 50%;
    background: var(--navy);
  }
  .brand-name {
    font-weight: 700;
    font-size: 38px;
    letter-spacing: 1px;
    text-transform: uppercase;
    color: var(--navy);
  }
  .services-band {
    position: absolute;
    left: 0;
    right: 0;
    bottom: 0;
    height: 78px;
    background: var(--navy);
    color: var(--white);
  }
  .services {
    position: absolute;
    left: 42px;
    top: 17px;
    list-style: none;
    display: grid;
    grid-template-columns: 223px auto;
    font-size: 16px;
    line-height: 20px;
  }
  .services li::before {
    content: "";
    display: inline-block;
    width: 7px;
    height: 7px;
    border-radius: 50%;
    background: var(--white);
    margin-right: 5px;
    vertical-align: 2px;
  }
</style>
</head>
<body>
<main class="canvas">

  <section class="card card-front" aria-label="Business card front">
    <div class="brand-mark-area" role="img" aria-label="Large company brand mark in white on navy"></div>
    <div class="person">
      <h1 class="person-name">DR COLIN HARTE</h1>
      <p class="person-role">R&amp;D Engineer</p>
    </div>
    <address class="address">
      PO Box XXX<br>
      Kelsby ACT 2917, Australia
    </address>
    <ul class="contact-list">
      <li>
        <svg class="contact-icon" viewBox="0 0 12 12" aria-hidden="true"><path d="M1 3c0-1 1-2 5-2s5 1 5 2v1H8V3H4v1H1zM3 5h6l2 3v3H1V8z"/></svg>
        0427 563 710
      </li>
      <li>
        <svg class="contact-icon" viewBox="0 0 12 12" aria-hidden="true"><path d="M1 2h10v8H1z M1.8 3 6 6.4 10.2 3" fill="none" stroke="#fff" stroke-width="1.2"/></svg>
        colin@wombarradevices.com.au
      </li>
      <li>
        <svg class="contact-icon" viewBox="0 0 12 12" aria-hidden="true"><circle cx="6" cy="6" r="5.5"/><path d="M3 4h3v3H4zM7 7h2v2H7z" fill="#03215f"/></svg>
        www.wombarradevices.com.au
      </li>
    </ul>
  </section>

  <section class="card card-back" aria-label="Business card back">
    <div class="brand">
      <span class="brand-dot" aria-hidden="true"></span>
      <span class="brand-name">Wombarra Devices</span>
    </div>
    <div class="services-band">
      <ul class="services">
        <li>Applied electromagnetics</li>
        <li>RF and high speed electronics</li>
        <li>Signal and image processing</li>
        <li>Electro-optical and laser systems</li>
      </ul>
    </div>
  </section>

</main>
</body>
</html>
```